Resposive web site in 4 languages + image gallery + logo design

We need a web page, which will work on all devices.
I have uploaded web page concept.
Company name: Praxelun
Industry/Entity Type
It Company
Logo Text
quality matters
Coding
Coded - Design and coding required
Number of Pages Required
1 page

```html
<!DOCTYPE html>
<html lang="en">
<head>
<meta charset="utf-8">
<title>Praxelun</title>
<link href="https://fonts.googleapis.com/css2?family=Roboto:wght@400;500;700&family=Lato:wght@400;700&display=swap" rel="stylesheet">
<style>
:root{
  --orange:#f7941d;
  --navy:#1d4e7e;
  --navy-dark:#1f3a5c;
  --text:#444444;
  --light:#f1f1f1;
  --mid:#e2e2e2;
  --footer:#333333;
  --footer-bottom:#1e1e1e;
  --white:#ffffff;
}
*{box-sizing:border-box;margin:0;padding:0}
html,body{width:1200px;height:2795px;overflow:hidden}
body{position:relative;background:var(--white);font-family:'Lato',sans-serif;color:var(--text)}
.abs{position:absolute}
.topbar{left:0;top:0;width:1200px;height:39px;background:var(--orange)}
.social{top:0;height:39px;width:32px;background:#e3861a;border-left:1px solid #f0a54a}
.social span{display:block;width:11px;height:11px;margin:14px auto;background:var(--navy-dark);border-radius:2px}
.lang{left:982px;top:0;width:119px;height:39px;background:var(--navy-dark);color:#fff;font:400 15px 'Lato',sans-serif;display:flex;align-items:center;gap:8px;padding-left:12px}
.lang .dot{width:14px;height:14px;border-radius:50%;background:#e6e6e6;border:2px solid #c0392b}
.header{left:0;top:39px;width:1200px;height:103px;background:#fff}
.brand{left:96px;top:74px;display:flex;align-items:center;gap:12px;font:700 34px 'Roboto',sans-serif;color:var(--orange)}
.brand i{width:22px;height:22px;background:var(--navy)}
.nav{top:94px;font:500 14px 'Roboto',sans-serif;color:#555;letter-spacing:.3px}
.nav.active{color:var(--navy)}
.nav-mark{left:654px;top:137px;width:38px;height:5px;background:var(--navy-dark)}
.hero{left:0;top:142px;width:1200px;height:464px;
  background:linear-gradient(172deg,#4b3b30 0%,#6e5b4c 22%,#8d7b6c 38%,#5a4538 52%,#3a2a22 62%,#8e8780 78%,#c9c4bd 92%,#a7a199 100%)}
.hero-title{left:0;top:348px;width:1200px;text-align:center;font:500 37px 'Roboto',sans-serif;color:#fff;text-shadow:0 1px 3px rgba(0,0,0,.35)}
.btn-quote{left:505px;top:428px;width:188px;height:42px;background:var(--orange);color:#fff;font:500 18px 'Roboto',sans-serif;display:flex;align-items:center;justify-content:center;letter-spacing:.5px}
.dots{left:561px;top:565px;display:flex;gap:8px}
.dots span{width:14px;height:14px;border-radius:50%;background:#ddd}
.dots span:first-child{background:var(--orange)}
.section-title{left:0;width:1200px;text-align:center;font:500 31px 'Roboto',sans-serif;color:var(--navy)}
.section-title b{color:var(--orange);font-weight:500}
.rule{left:399px;width:402px;height:2px;background:#8fa7c0}
.about-text{left:112px;top:734px;width:976px;text-align:center;font:400 13px/22px 'Lato',sans-serif;color:#444}
.btn-more{left:540px;top:835px;width:118px;height:33px;border:1.5px solid var(--orange);color:var(--orange);font:400 14px 'Lato',sans-serif;display:flex;align-items:center;justify-content:center}
.band{left:0;width:1200px}
.thumb{width:83px;height:76px;border:2px solid #fff;box-shadow:0 0 2px #999}
.arrow{width:0;height:0;border-left:6px solid transparent;border-right:6px solid transparent}
.arrow.up{border-bottom:7px solid #777}
.arrow.down{border-top:7px solid #777}
.svc-title{font:500 23px 'Roboto',sans-serif;color:var(--navy)}
.svc-text{width:430px;font:400 13px/27px 'Lato',sans-serif;color:#444}
.footer{left:0;top:2455px;width:1200px;height:297px;background:var(--footer)}
.f-head{top:2496px;display:flex;align-items:center;gap:10px;font:500 19px 'Roboto',sans-serif;color:#fff}
.f-line{top:2532px;height:1px;background:#666}
.f-line i{display:block;width:80px;height:2px;background:var(--orange)}
.field{border:1.5px solid #ddd;color:#eee;font:400 13px 'Lato',sans-serif;padding:10px 10px}
.submit{left:337px;top:2664px;width:214px;height:43px;background:var(--orange);color:#fff;font:700 14px 'Roboto',sans-serif;display:flex;align-items:center;justify-content:center}
.vdiv{top:2492px;width:1px;height:225px;background:#555}
.qlink{left:618px;font:400 14px 'Lato',sans-serif;color:#eee}
.qlink.strong{font-weight:700}
.contact{left:859px;font:400 13px/17px 'Lato',sans-serif;color:#eee;display:flex;gap:14px}
.copy{left:0;top:2752px;width:1200px;height:43px;background:var(--footer-bottom);color:#ddd;font:400 12px 'Lato',sans-serif;display:flex;align-items:center;justify-content:center}
</style>
</head>
<body>

<div class="abs topbar"></div>
<div class="abs social" style="left:855px"><span></span></div>
<div class="abs social" style="left:887px"><span></span></div>
<div class="abs social" style="left:919px"><span></span></div>
<div class="abs social" style="left:951px"><span></span></div>
<div class="abs lang"><span class="dot"></span>English
  <svg width="10" height="6" viewBox="0 0 10 6"><path d="M0 0h10L5 6z" fill="#fff"/></svg></div>

<header class="abs header"></header>
<div class="abs brand"><i></i>Praxelun</div>
<div class="abs nav active" style="left:651px">HOME</div>
<div class="abs nav-mark"></div>
<div class="abs nav" style="left:751px">SERVICES</div>
<div class="abs nav" style="left:879px">ABOUT US</div>
<div class="abs nav" style="left:1010px">CONTACT US</div>

<div class="abs hero" role="img" aria-label="Photo of a modern kitchen with dark wood cabinets, pendant lights and a dining table"></div>
<div class="abs hero-title">Are you interested in an estimate?</div>
<div class="abs btn-quote">GET A QUOTE</div>
<div class="abs dots"><span></span><span></span><span></span><span></span></div>

<h2 class="abs section-title" style="top:655px"><b>ABOUT</b> PRAXELUN</h2>
<div class="abs rule" style="top:712px"></div>
<p class="abs about-text">Lorem ipsum dolor sit amet, consectetuer adipiscing elit, sed diam nonummy nibh euismod tincidunt ut laoreet dolore magna aliquam erat volutpat. Ut wisi enim ad minim veniam, quis nostrud exerci tation ullamcorper suscipit lobortis nisl ut aliquip ex ea commodo consequat. Duis autem vel eum iriure dolor in amet, consectetuer adipiscing elit, sed diam nonummy nibh euismod tincidunt ut laoreet dolore amet, consectetuer adipiscing elit, sed diam nonummy nibh euismod tincidunt ut l</p>
<div class="abs btn-more">Learn More ››</div>

<section class="abs band" style="top:926px;height:570px;background:var(--light)"></section>
<h2 class="abs section-title" style="top:979px"><b>OUR</b> SERVICES</h2>
<div class="abs rule" style="top:1034px"></div>
<div class="abs" style="left:99px;top:1094px;width:415px;height:341px;background:linear-gradient(90deg,#5e1f1b 0%,#7a3a22 10%,#c49a6a 18%,#b98040 30%,#d09a55 50%,#b98040 70%,#c49a6a 82%,#7a3a22 90%,#5e1f1b 100%)" role="img" aria-label="Photo of a honey oak front door with frosted side glass panels"></div>
<div class="abs arrow up" style="left:572px;top:1080px"></div>
<div class="abs thumb" style="left:537px;top:1094px;background:linear-gradient(160deg,#2c2622,#7a5a3e 60%,#3a302a)" role="img" aria-label="Thumbnail of stacked wood planks"></div>
<div class="abs thumb" style="left:537px;top:1180px;background:linear-gradient(90deg,#8a3a26,#c08a4a 50%,#8a3a26)" role="img" aria-label="Thumbnail of wooden door"></div>
<div class="abs thumb" style="left:537px;top:1267px;background:linear-gradient(90deg,#f2efe8,#7a3a22 30%,#7a3a22 70%,#f2efe8)" role="img" aria-label="Thumbnail of double glass doors"></div>
<div class="abs thumb" style="left:537px;top:1356px;background:linear-gradient(140deg,#e0c8a8,#a0582a 55%,#6a3018)" role="img" aria-label="Thumbnail of wooden spiral staircase"></div>
<div class="abs arrow down" style="left:572px;top:1440px"></div>
<h3 class="abs svc-title" style="left:665px;top:1119px">WOODWORKS</h3>
<p class="abs svc-text" style="left:665px;top:1170px">Lorem ipsum dolor sit amet, consectetuer adipiscing elit, sed diam nonummy nibh euismod tincidunt ut laoreet dolore magna aliquam erat volutpat. Ut wisi enim ad minim veniam, quis nostrud exerci tation ullamcorper suscipit lobortis nisl ut aliquip ex ea commodo consequat. Duis autem vel eum iriure dolor in hendrerit in vulputate velit esse molestie consequat, vel illum dolore eu feugiat nulla facilisis at vero eros et accumsan et iusto odio dignissim qui blandit praesent luptatum zzril delenit augue duis dolore te feugait nulla facilisi.</p>

<section class="abs band" style="top:1496px;height:479px;background:var(--mid)"></section>
<h3 class="abs svc-title" style="left:99px;top:1589px">STONEWORKS</h3>
<p class="abs svc-text" style="left:99px;top:1640px">Lorem ipsum dolor sit amet, consectetuer adipiscing elit, sed diam nonummy nibh euismod tincidunt ut laoreet dolore magna aliquam erat volutpat. Ut wisi enim ad minim veniam, quis nostrud exerci tation ullamcorper suscipit lobortis nisl ut aliquip ex ea commodo consequat. Duis autem vel eum iriure dolor in hendrerit in vulputate velit esse molestie consequat, vel illum dolore eu feugiat nulla facilisis at vero eros et accumsan et iusto odio dignissim qui blandit praesent luptatum zzril delenit augue duis dolore te feugait nulla facilisi.</p>
<div class="abs arrow up" style="left:609px;top:1551px"></div>
<div class="abs thumb" style="left:574px;top:1565px;background:linear-gradient(180deg,#b8c4cc,#8a8878 45%,#6a7a4a)" role="img" aria-label="Thumbnail of stone patio"></div>
<div class="abs thumb" style="left:574px;top:1652px;background:linear-gradient(150deg,#8a8470,#5e5a48 60%,#7a7460)" role="img" aria-label="Thumbnail of polished stone floor"></div>
<div class="abs thumb" style="left:574px;top:1740px;background:linear-gradient(180deg,#8a5a4a,#a07a6a 50%,#5a7a3a)" role="img" aria-label="Thumbnail of paved walkway"></div>
<div class="abs thumb" style="left:574px;top:1829px;background:linear-gradient(180deg,#c8ccd0,#7a786e 50%,#5a584e)" role="img" aria-label="Thumbnail of stone outdoor kitchen"></div>
<div class="abs arrow down" style="left:609px;top:1911px"></div>
<div class="abs" style="left:684px;top:1565px;width:417px;height:341px;background:linear-gradient(170deg,#8c7a72 0%,#6b4a3c 22%,#eeeae4 30%,#7a5040 38%,#4e6a30 50%,#9a7468 62%,#b08e80 75%,#8e6a5e 86%,#5f8a3a 100%)" role="img" aria-label="Photo of a curved brick paver walkway leading to a white front door among garden beds"></div>

<section class="abs band" style="top:1975px;height:480px;background:var(--light)"></section>
<div class="abs" style="left:99px;top:2042px;width:415px;height:339px;background:linear-gradient(90deg,#2a3424 0%,#4a4030 12%,#7a3e1c 22%,#a9652e 38%,#bd7a3c 50%,#a9652e 62%,#7a3e1c 78%,#4a4030 88%,#2a3424 100%)" role="img" aria-label="Photo of a restored wooden double entrance door flanked by lanterns and shrubs"></div>
<div class="abs arrow up" style="left:572px;top:2028px"></div>
<div class="abs thumb" style="left:537px;top:2042px;background:linear-gradient(180deg,#c8b090,#6a4a36 55%,#3e2c22)" role="img" aria-label="Thumbnail of bedroom interior"></div>
<div class="abs thumb" style="left:537px;top:2128px;background:linear-gradient(90deg,#3a2c20,#a0602a 50%,#3a2c20)" role="img" aria-label="Thumbnail of wooden entrance door"></div>
<div class="abs thumb" style="left:537px;top:2216px;background:linear-gradient(180deg,#d8ccbc,#f4f0ea 45%,#a89886)" role="img" aria-label="Thumbnail of white window frames"></div>
<div class="abs thumb" style="left:537px;top:2305px;background:linear-gradient(140deg,#eae2d6,#b89878 55%,#6a4a30)" role="img" aria-label="Thumbnail of staircase"></div>
<div class="abs arrow down" style="left:572px;top:2388px"></div>
<h3 class="abs svc-title" style="left:665px;top:2066px">RESTORATION</h3>
<p class="abs svc-text" style="left:665px;top:2117px">Lorem ipsum dolor sit amet, consectetuer adipiscing elit, sed diam nonummy nibh euismod tincidunt ut laoreet dolore magna aliquam erat volutpat. Ut wisi enim ad minim veniam, quis nostrud exerci tation ullamcorper suscipit lobortis nisl ut aliquip ex ea commodo consequat. Duis autem vel eum iriure dolor in hendrerit in vulputate velit esse molestie consequat, vel illum dolore eu feugiat nulla facilisis at vero eros et accumsan et iusto odio dignissim qui blandit praesent luptatum zzril delenit augue duis dolore te feugait nulla facilisi.</p>

<footer class="abs footer"></footer>
<div class="abs f-head" style="left:99px">
  <svg width="20" height="20" viewBox="0 0 20 20"><rect x="2" y="4" width="16" height="14" fill="none" stroke="#fff" stroke-width="2"/><path d="M2 8h16M6 2v4M14 2v4" stroke="#fff" stroke-width="2"/></svg>Quick Inquiry</div>
<div class="abs f-line" style="left:99px;width:452px"><i></i></div>
<div class="abs field" style="left:99px;top:2545px;width:212px;height:41px">Name</div>
<div class="abs field" style="left:99px;top:2604px;width:212px;height:43px">Phone</div>
<div class="abs field" style="left:99px;top:2664px;width:212px;height:43px">Email</div>
<div class="abs field" style="left:337px;top:2545px;width:214px;height:102px">Message</div>
<div class="abs submit">SUBMIT</div>

<div class="abs vdiv" style="left:583px"></div>
<div class="abs f-head" style="left:618px">
  <svg width="18" height="20" viewBox="0 0 18 20"><rect x="2" y="2" width="14" height="17" fill="none" stroke="#fff" stroke-width="2"/><path d="M5 7h8M5 11h8M5 15h6" stroke="#fff" stroke-width="1.5"/></svg>Quick Links</div>
<div class="abs f-line" style="left:618px;width:178px"><i></i></div>
<div class="abs qlink strong" style="top:2546px">› Home</div>
<div class="abs qlink" style="top:2591px">› Services</div>
<div class="abs qlink" style="top:2634px">› About Us</div>
<div class="abs qlink" style="top:2677px">› Contact Us</div>

<div class="abs vdiv" style="left:827px"></div>
<div class="abs f-head" style="left:859px">
  <svg width="20" height="20" viewBox="0 0 20 20"><circle cx="10" cy="10" r="8" fill="none" stroke="#fff" stroke-width="2"/><path d="M2 10h16M10 2c-4 4-4 12 0 16M10 2c4 4 4 12 0 16" fill="none" stroke="#fff" stroke-width="1.5"/></svg>Contact Details</div>
<div class="abs f-line" style="left:859px;width:226px"><i></i></div>
<div class="abs contact" style="top:2551px">
  <svg width="12" height="18" viewBox="0 0 12 18"><path d="M6 0a6 6 0 0 1 6 6c0 5-6 12-6 12S0 11 0 6a6 6 0 0 1 6-6z" fill="#fff"/><circle cx="6" cy="6" r="2.2" fill="#333"/></svg>
  <div><b style="font-weight:700">Praxelun</b><br>Lorem ipsum dolor sit consec tetuer<br>adipiscing elit, sed diam</div></div>
<div class="abs contact" style="top:2628px">
  <svg width="13" height="13" viewBox="0 0 13 13"><path d="M3 0l2 3-1.5 1.5a8 8 0 0 0 5 5L10 8l3 2-1.5 3C5 13 0 8 0 1.5z" fill="#fff"/></svg>
  <div>+100 00 24680</div></div>
<div class="abs contact" style="top:2675px">
  <svg width="14" height="10" viewBox="0 0 14 10"><rect width="14" height="10" fill="#fff"/><path d="M0 0l7 6 7-6" fill="none" stroke="#333" stroke-width="1.3"/></svg>
  <div style="font-size:12px">sales@praxelun-mail.com</div></div>

<div class="abs copy">Copyright © 2016 Praxelun. All Right Reserved.</div>

</body>
</html>
```